Quorva - corporate Business Card

We need a good look and innovative business card for a new start up company based in Los Angeles called "Quorva". We are in a payment business, including payment card, app, and ewallet. We are expert in online payment and Card not present (CNP) transaction.
We need an innovative, modern business card.

Our logo font is Aero Matics

Target Market(s)

Startup - Bank - Online Payment - Card Manufacturing

Industry/Entity Type

Startup

Contact Information for Business Card

phone: 555 014 7396 - Address: 4172 Marlowe blvd, Dunmere Park, OR 97299

Requirements
Must have
• Message: innovative, professional, expert, high tech, trust, online payment expert, security
Nice to have
• no comment
Should not have
• no Comment

```html
<!DOCTYPE html>
<html lang="en">
<head>
<meta charset="utf-8">
<title>Quorva – Business Card</title>
<link rel="stylesheet" href="https://fonts.googleapis.com/css2?family=Exo+2:wght@500;600;700&family=Hind:wght@400;500&display=swap">
<style>
  :root {
    --brand-red: #b81f2d;
    --card-white: #ffffff;
    --ink-grey: #4a4a4a;
    --backdrop: #ece9e4;
  }
  * { box-sizing: border-box; margin: 0; padding: 0; }
  html, body { width: 1200px; height: 843px; overflow: hidden; }
  body { background: var(--backdrop); position: relative; }

  .card {
    position: absolute;
    top: 253px;
    width: 558px;
    height: 318px;
    border-radius: 14px;
    overflow: hidden;
    box-shadow: 0 3px 10px rgba(0,0,0,0.25);
  }
  .card--front { left: 28px; background: var(--card-white); }
  .card--back  { left: 614px; background: var(--brand-red); }

  .accent-bar {
    position: absolute; left: 0; top: 34px;
    width: 13px; height: 246px;
    background: var(--brand-red);
    border-radius: 0 4px 4px 0;
  }

  .brand { position: absolute; left: 26px; top: 34px; display: flex; align-items: center; gap: 8px; }
  .brand__dot { width: 50px; height: 50px; border-radius: 50%; background: var(--brand-red); }
  .brand__name {
    font-family: "Exo 2", sans-serif; font-weight: 600;
    font-size: 35px; color: var(--brand-red); line-height: 1;
  }

  .person { position: absolute; left: 26px; top: 100px; }
  .person__name {
    font-family: "Exo 2", sans-serif; font-weight: 700;
    font-size: 22px; color: var(--brand-red); line-height: 1.1; letter-spacing: 0.3px;
  }
  .person__title {
    font-family: "Hind", sans-serif; font-size: 15px; color: var(--ink-grey); line-height: 1.2;
  }

  .contact-list { position: absolute; left: 26px; top: 160px; list-style: none; }
  .contact-list li {
    display: flex; align-items: center; gap: 10px;
    height: 23px;
    font-family: "Hind", sans-serif; font-size: 15.5px; font-weight: 500;
    color: var(--ink-grey); letter-spacing: 0.3px;
  }
  .contact-list svg { width: 14px; height: 14px; fill: var(--brand-red); flex: none; }

  .address {
    position: absolute; left: 26px; top: 243px;
    font-family: "Hind", sans-serif; font-size: 15.5px; font-weight: 500;
    color: var(--ink-grey); line-height: 19px; letter-spacing: 0.3px;
  }

  .half-disc { position: absolute; border-radius: 50%; width: 316px; height: 316px; top: 1px; }
  .card--front .half-disc { left: 400px; background: var(--brand-red); }
  .card--back .half-disc  { left: -158px; background: var(--card-white); }

  .back-name {
    position: absolute; left: 206px; top: 100px;
    font-family: "Exo 2", sans-serif; font-weight: 600;
    font-size: 92px; line-height: 1; color: var(--card-white); letter-spacing: 1px;
  }
</style>
</head>
<body>
  <section class="card card--front">
    <div class="accent-bar"></div>
    <div class="brand">
      <span class="brand__dot"></span>
      <span class="brand__name">quorva</span>
    </div>
    <div class="person">
      <p class="person__name">Daniel Brennan</p>
      <p class="person__title">President</p>
    </div>
    <ul class="contact-list">
      <li>
        <svg viewBox="0 0 24 24"><path d="M6.6 10.8c1.4 2.8 3.8 5.1 6.6 6.6l2.2-2.2c.3-.3.7-.4 1-.2 1.1.4 2.3.6 3.6.6.6 0 1 .4 1 1V20c0 .6-.4 1-1 1C10.6 21 3 13.4 3 4c0-.6.4-1 1-1h3.5c.6 0 1 .4 1 1 0 1.3.2 2.5.6 3.6.1.3 0 .7-.2 1z"/></svg>
        555 014 7396
      </li>
      <li>
        <svg viewBox="0 0 24 24"><path d="M2 5h20v14H2z M4 7v.5l8 5 8-5V7l-8 5z" fill-rule="evenodd"/></svg>
        daniel@quorva.com
      </li>
      <li>
        <svg viewBox="0 0 24 24"><path d="M12 2a10 10 0 1 0 0 20 10 10 0 0 0 0-20zm6.9 6h-3a15 15 0 0 0-1.3-3.8A8 8 0 0 1 18.9 8zM12 4c.8 1.2 1.5 2.5 1.9 4h-3.8c.4-1.5 1.1-2.8 1.9-4zM4.3 14a8 8 0 0 1 0-4h3.4a16 16 0 0 0 0 4zm.8 2h3a15 15 0 0 0 1.3 3.8A8 8 0 0 1 5.1 16zm3-8h-3a8 8 0 0 1 4.3-3.8C8.8 5.4 8.4 6.7 8.1 8zM12 20c-.8-1.2-1.5-2.5-1.9-4h3.8c-.4 1.5-1.1 2.8-1.9 4zm2.3-6H9.7a14 14 0 0 1 0-4h4.6a14 14 0 0 1 0 4zm.3 5.8c.6-1.2 1-2.5 1.3-3.8h3a8 8 0 0 1-4.3 3.8zM16.3 14a16 16 0 0 0 0-4h3.4a8 8 0 0 1 0 4z"/></svg>
        www.quorva.com
      </li>
    </ul>
    <p class="address">4172 Marlowe blvd<br>Dunmere Park, OR 97299</p>
    <div class="half-disc"></div>
  </section>

  <section class="card card--back">
    <div class="half-disc"></div>
    <p class="back-name">quorva</p>
  </section>
</body>
</html>
```